Business Card Re-Design/Update

We'd like to update out business cards. I've included our current "Style guide" which has the colour scheme of the organisation in it. I've also included the branding files with logos etc in them.

I've also included a copy of one of our existing cards so that you can see how ugly/dated they look. I'd like a fresh modern corporate look.

Target Market(s)

These are for our clients, potential clients, industry contacts - like all business cards

Contact Information for Business Card

Name
Position
Company Address - Level 1, 47 Fernby Street, Carlow Qld 4072
Direct Phone
mobile
Email
Website -www.korvalit.com.au
Logo

Colors

Designer to choose colors to be used in the design.

Requirements
Must have
• Main Logo
• Cards will need to be editable to be able to personalize them for each new employee.
Nice to have
• The MapOut, ShipWell, KeepSteady would be okay to have if they can be sensibly and professionally added to the look without detracting from the main imagery.
• Maybe they could go on the back of the card? will leave this to your creative discretion as to whether/where they fit.
Should not have
• Should not have decorative or script fonts

```html
<!DOCTYPE html>
<html lang="en">
<head>
<meta charset="utf-8">
<title>korvalIT business card</title>
<link rel="stylesheet" href="https://fonts.googleapis.com/css2?family=Arimo:wght@400&family=Montserrat:wght@500;600&display=swap">
<style>
  :root {
    --backdrop: #666666;
    --card-white: #ffffff;
    --brand-red: #d71920;
    --charcoal: #3a3a3c;
    --ink: #2b2b2b;
    --rule: #8a8a8a;
  }
  html, body {
    margin: 0;
    padding: 0;
    width: 1200px;
    height: 802px;
    overflow: hidden;
    background: var(--backdrop);
  }
  .canvas {
    position: relative;
    width: 1200px;
    height: 802px;
  }
  .card {
    position: absolute;
    top: 274px;
    width: 442px;
    height: 265px;
    overflow: hidden;
  }
  .card-front { left: 136px; background: var(--card-white); }
  .card-back { left: 624px; background: var(--brand-red); }

  /* front */
  .brand {
    position: absolute;
    left: 0;
    top: 96px;
    width: 203px;
    text-align: center;
  }
  .brand-square {
    display: block;
    width: 22px;
    height: 22px;
    margin: 0 auto 10px;
    background: var(--brand-red);
  }
  .brand-name {
    font-family: "Montserrat", sans-serif;
    font-weight: 500;
    font-size: 28px;
    line-height: 1;
    color: var(--charcoal);
    letter-spacing: -0.3px;
  }
  .divider {
    position: absolute;
    left: 203px;
    top: 59px;
    width: 1px;
    height: 148px;
    background: var(--rule);
  }
  .details {
    position: absolute;
    left: 220px;
    top: 58px;
    font-family: "Arimo", sans-serif;
    color: var(--ink);
  }
  .person-name {
    font-family: "Montserrat", sans-serif;
    font-weight: 600;
    font-size: 15.5px;
    line-height: 1;
    color: var(--brand-red);
    margin: 0;
  }
  .person-role {
    font-size: 12.5px;
    line-height: 1;
    margin: 2px 0 10px;
  }
  .contact-list {
    list-style: none;
    margin: 0;
    padding: 0;
    font-size: 12.5px;
  }
  .contact-list li {
    display: flex;
    align-items: center;
    height: 15.5px;
  }
  .contact-icon {
    width: 10px;
    height: 10px;
    margin-right: 4px;
    fill: var(--brand-red);
    flex: none;
  }
  .address {
    font-size: 12.5px;
    line-height: 15.5px;
    margin: 7px 0 0;
    font-style: normal;
  }

  /* back */
  .back-field {
    position: absolute;
    inset: 0;
  }
  .service-list {
    position: absolute;
    right: 27px;
    top: 68px;
    margin: 0;
    padding: 0;
    list-style: none;
    text-align: right;
  }
  .service-list li {
    display: flex;
    align-items: center;
    justify-content: flex-end;
    height: 46px;
    font-family: "Montserrat", sans-serif;
    font-weight: 500;
    font-size: 26px;
    color: var(--card-white);
  }
  .service-square {
    width: 13px;
    height: 13px;
    margin-right: 9px;
    background: var(--card-white);
  }
</style>
</head>
<body>
<div class="canvas">

  <section class="card card-front">
    <div class="brand">
      <span class="brand-square"></span>
      <div class="brand-name">korvalIT</div>
    </div>

    <div class="divider"></div>

    <div class="details">
      <h1 class="person-name">DANA WHITFIELD</h1>
      <p class="person-role">Business Development Manager</p>
      <ul class="contact-list">
        <li>
          <svg class="contact-icon" viewBox="0 0 10 10"><path d="M1 4 Q5 0 9 4 L8 5 L6.5 4.2 L6.5 3.4 Q5 3 3.5 3.4 L3.5 4.2 L2 5 Z"/><rect x="2.5" y="5" width="5" height="3.5" rx="0.5"/></svg>
          +61 (0)412 555 038
        </li>
        <li>
          <svg class="contact-icon" viewBox="0 0 10 10"><path d="M3 0.5 H7 a1 1 0 0 1 1 1 V8.5 a1 1 0 0 1 -1 1 H3 a1 1 0 0 1 -1 -1 V1.5 a1 1 0 0 1 1 -1 Z M3.2 1.8 V7.5 H6.8 V1.8 Z"/></svg>
          +61 (0)7 3000 4182
        </li>
        <li>
          <svg class="contact-icon" viewBox="0 0 10 10"><rect x="2.5" y="0.5" width="5" height="3"/><rect x="0.5" y="3.5" width="9" height="4" rx="0.8"/><rect x="2.5" y="6.5" width="5" height="3"/></svg>
          +61 (0)7 3000 4190
        </li>
        <li>
          <svg class="contact-icon" viewBox="0 0 10 10"><path d="M0.5 2 H9.5 V8 H0.5 Z M1 2.5 L5 5.5 L9 2.5" /></svg>
          dwhitfield@korvalit.com.au
        </li>
        <li>
          <svg class="contact-icon" viewBox="0 0 10 10"><circle cx="5" cy="5" r="4.5"/></svg>
          www.korvalit.com.au
        </li>
      </ul>
      <address class="address">Level 1, 47 Fernby Street<br>Carlow Qld 4072</address>
    </div>
  </section>

  <section class="card card-back">
    <svg class="back-field" viewBox="0 0 442 265" aria-hidden="true">
      <polygon points="0,0 131,0 263,132 131,265 0,265" fill="var(--charcoal)"/>
    </svg>
    <ul class="service-list">
      <li><span class="service-square"></span>KeepSteady</li>
      <li><span class="service-square"></span>MapOut</li>
      <li><span class="service-square"></span>ShipWell</li>
    </ul>
  </section>

</div>
</body>
</html>
```